Local Flower Farm Needs Business Card Design

I need business cards designed for a flower farm based in Eudora, Kansas.
Business Info:
We are a local cut flower farm located in Eudora, Kansas, founded by Corinne Haldwick. What started as a passion for agriculture and search for more joy in daily life has blossomed into a small business dedicated to providing the community with beautiful, fresh, and sustainable flowers. We specialize in local, seasonal blooms, ensuring that every petal reflects the care and dedication we pour into our craft. Our mission is to deliver the highest quality flowers directly to our customers through local farmers markets and to florists who share our commitment to sustainability. Join us in celebrating the beauty of nature, one bloom at a time!
Contact Details:
Corinne Haldwick
Owner
Phone 913-555-0147
Facebook: Rosalind Thorpe Gardens
Instagram: @RosalindThorpeGardens
Website: RosalindThorpeGardens.example
Target Market(s)
Wholesale to Florists and Direct to Consumer via Farmers Market
Industry/Entity Type
Florist, Farm
Contact Information for Business Card
Name, Contact Info, Logo
Look and feel
Each slider illustrates characteristics of the customer's brand and the style your logo design should communicate.

```html
<!DOCTYPE html>
<html lang="en">
<head>
<meta charset="utf-8">
<title>Rosalind Thorpe Gardens – Business Card</title>
<link href="https://fonts.googleapis.com/css2?family=Montserrat:wght@400;500;700;800&display=swap" rel="stylesheet">
<style>
  :root {
    --stage: #a3a3a3;
    --ink-deep: #08272c;
    --paper: #ffffff;
    --teal-glow: #4fc6e6;
    --teal-mid: #2b6f7c;
    --text-light: #ffffff;
  }
  * { margin: 0; padding: 0; box-sizing: border-box; }
  html, body {
    width: 1093px; height: 1200px; overflow: hidden;
    background: var(--stage);
    font-family: "Montserrat", sans-serif;
  }
  .card {
    position: absolute; left: 264px; width: 598px; height: 364px;
    border-radius: 15px; overflow: hidden; background: var(--ink-deep);
  }
  .card--front { top: 224px; }
  .card--back { top: 615px; height: 368px; }
  .card__shape { position: absolute; inset: 0; }
  .holder { position: absolute; left: 30px; top: 40px; color: var(--text-light); }
  .holder__name { font-weight: 800; font-size: 22px; letter-spacing: 0.2px; line-height: 1.1; }
  .holder__role { font-weight: 400; font-size: 13px; margin-top: 2px; }
  .contacts { position: absolute; left: 30px; top: 254px; list-style: none; color: var(--text-light); }
  .contacts__item { display: flex; align-items: center; gap: 8px; font-size: 13px; height: 21.8px; }
  .contacts__icon { width: 12px; height: 12px; flex: none; }
  .brand-mark {
    position: absolute; left: 362px; top: 90px; width: 210px; height: 210px;
    border: 1.5px solid var(--ink-deep); border-radius: 50%;
    display: flex; align-items: center; justify-content: center; text-align: center;
    color: var(--ink-deep); font-weight: 700; font-size: 22px; line-height: 1.2;
  }
  .pattern {
    position: absolute; inset: 0;
    background: linear-gradient(125deg, var(--teal-glow) 0%, var(--teal-mid) 22%, var(--ink-deep) 52%, var(--ink-deep) 100%);
  }
  .back-mark {
    position: absolute; left: 398px; top: 236px; width: 80px; text-align: center;
    color: var(--text-light); font-weight: 700; font-size: 12px; line-height: 1.2;
  }
</style>
</head>
<body>
  <section class="card card--front" aria-label="Business card front">
    <svg class="card__shape" viewBox="0 0 598 364" aria-hidden="true">
      <path d="M449,0 C340,70 290,130 290,186 C290,250 340,300 446,364 L598,364 L598,0 Z" fill="var(--paper)"/>
      <path d="M415,36 C340,80 311,140 311,190 C311,240 340,290 415,332 C355,290 325,240 325,192 C325,140 355,85 415,36 Z" fill="var(--ink-deep)"/>
    </svg>
    <div class="holder">
      <h1 class="holder__name">Corinne Haldwick</h1>
      <p class="holder__role">Owner</p>
    </div>
    <ul class="contacts">
      <li class="contacts__item">
        <svg class="contacts__icon" viewBox="0 0 24 24" aria-hidden="true"><path fill="#fff" d="M6.6 10.8a15.1 15.1 0 0 0 6.6 6.6l2.2-2.2a1 1 0 0 1 1-.25 11.4 11.4 0 0 0 3.6.57 1 1 0 0 1 1 1V20a1 1 0 0 1-1 1A17 17 0 0 1 3 4a1 1 0 0 1 1-1h3.5a1 1 0 0 1 1 1c0 1.25.2 2.45.57 3.57a1 1 0 0 1-.25 1z"/></svg>
        913-555-0147
      </li>
      <li class="contacts__item">
        <svg class="contacts__icon" viewBox="0 0 12 12" aria-hidden="true"><circle cx="6" cy="6" r="6" fill="#fff"/></svg>
        Rosalind Thorpe Gardens
      </li>
      <li class="contacts__item">
        <svg class="contacts__icon" viewBox="0 0 12 12" aria-hidden="true"><circle cx="6" cy="6" r="6" fill="#fff"/></svg>
        @RosalindThorpeGardens
      </li>
      <li class="contacts__item">
        <svg class="contacts__icon" viewBox="0 0 24 24" aria-hidden="true"><circle cx="12" cy="12" r="10" fill="none" stroke="#fff" stroke-width="2.4"/><path d="M2 12h20M12 2c3 3 4 6.5 4 10s-1 7-4 10c-3-3-4-6.5-4-10s1-7 4-10z" fill="none" stroke="#fff" stroke-width="2"/></svg>
        www.RosalindThorpeGardens.example
      </li>
    </ul>
    <div class="brand-mark">Rosalind<br>Thorpe<br>Gardens</div>
  </section>

  <section class="card card--back" aria-label="Business card back">
    <div class="pattern" role="img" aria-label="Repeating monogram pattern fading from bright teal to deep green"></div>
    <div class="back-mark">Rosalind Thorpe Gardens</div>
  </section>
</body>
</html>
```